Corporate website design needed

We need a Contemporary Industrial/Tech/Logistics Website design to match our logistic client's business. Our client consults and build logistics solutions that they manage but they are not a typical 3PL (3rd party logistics company) which is primarily engaged in moving boxes.
PSD file only for now, home and default templates.
COMPANY CHARACTER
DESIGN LOOK AND FEEL
• The design should also be modern and visually well organized — employing a combination of visual devices and info graphics. Keep it light and not too heavy but strong/ professional. And unique.
• The design should go beyond the typical industrial pick and pack 3PL representing [Logistics Company] as a High Tech/IT logistics company.
Some examples although these are not right for this client because they have much more content and present themselves more as a 3pl.
http://www.vobrelink-hub.example/ (More right then wrong - Like this but simplified)
http://www.durmaxfreight.example (Ugly)
http://www.tpwallerton.example (More right then wrong but different focus)
http://www.pelhamrye.example/ Too 3PL trucking… We want a bit ore high level approach
The difference, the design should be a fusion in core concepts that culminate in a design which implies the following attributes. Tech (Big data / analytics / software), Consultancy (Solutions, SME, Leader), 3PL Industry vertical solutions.
NOTE: The visualization of “tech” is not “1” and “0”, but more “software and analytics” Perhaps more like www.navimetra.example.
• They need to be seen as a solutions provider in Logistics and as in Subject matter experts
TONE
The tone needs to exude professionalism, expertise, though leadership along with technical and executional excellence.
Experienced
Knowledgeable
Confident
Determined
Straightforward
WEBSITE OBJECTIVES
• Focus C-Suite executives and logistics managers’ attention on [Logistics Company]s commanding knowledge and expertise, and unique approach to supply chain solutions producing more RFP wins
• Create an easy to scan design which decreases the reliance on text through featured text, summaries, and smaller “chunked” size bits of information.
• Convey [Logistics Company] as high-tech 3PL solutions developer and services provider with a ‘high-touch’ consultative approach.
• Showcase [Logistics Company]’s value propositions. (See Slider Content)
• Showcase [Logistics Company]’s expertise in logistical analytics.
• Gain recognition as an industry leader in evolutionary new space (supply chain 2.0)
WEBSITE STRATEGY
• Reduce reliance on text (at least within initial entry points for each section)
• Typography: Watch text line lengths and readability, bolder fonts. NO SERIFS
• Generally, create a click-through format so that users who want more details can find it, and those who don’t can get a snapshot without clicking through.
• Increase visual content through info graphics and some dynamic content, photography
• Better utilize the space on each page (e.g., add visual interest, photography and iconography where appropriate to break up copy blocks and maintain readable line lengths).
COLOR SCHEME
• Create a more engaging color scheme (the logo will remain the same under all circumstances).
• Red / grayscale may work…. Not too dark or heavy. Not too much red. Ex. quiltora.example
• Also try blues and greys. They seem to like that. Open to suggestions but don’t get to crazy. Red is in their logo but too much may be a problem.
PHOTOGRAPHY
Yes. And I will upload some.
If you pick photography please be sure to note Which stock house used and the image number!
CONTENT
The content will be presented in a more hierarchical format — with lead-ins, paragraph and section headers and navigational cues to expand lengthier content allowing the visitor to more easily scan the website. No case studies, No Social media, News while on the home page should not be over emphasized. They don't post a lot so it gets dated quickly ...
I will be uploading a wire frame and other elements.
NOTE: I uploaded my EXAMPLE mock up which is close but not close enough.
I am not a great designer. So I am looking for an alternative that exceed my design ability! These examples show the basic layout but I really want some varied alternatives.
The colors are inconsistent and type not quite right. The grey bar at top is not right and should probably go away.
Please pull the basic elements in the example together into a great design.
If you have questions please contact me.
i will upload some photography tomorrow that may be of use.
Thanks!
Updates
Hi All,
We are still evaluating the submitted designs. Sorry for the delay.
Target Market(s)
This website is primarily a validation website. Few new customers will search and find them as such...
The site should be Focused on C-Suite executives and logistics managers’ attention on [Logistics Company]s commanding knowledge and expertise, and unique approach to supply chain solutions producing more RFP wins
Industry/Entity Type
Business
Font styles to use
Requirements
Must have
- Slide show, Clearly explain who they are and what they do.
Create an easy to scan design which decreases the reliance on text through featured text, summaries, and smaller “chunked” size bits of information.
Convey [Logistics Company] as high-tech 3PL solutions developer and services
provider with a ‘high-touch’ consultative approach.
Should not have
- No Ads space
No Social media
Not too cluttered. Keep it clean.

```html
<!DOCTYPE html>
<html lang="en">
<head>
<meta charset="utf-8">
<title>Northvale Logistics</title>
<link href="https://fonts.googleapis.com/css2?family=Open+Sans:wght@400;600;700&display=swap" rel="stylesheet">
<style>
:root{
  --red:#c8102e;
  --ink:#2b2b2b;
  --text:#7a7a7a;
  --nav:#4b4e53;
  --hero-a:#0a3f74;
  --hero-b:#1d87c6;
  --tabs:#2a2b2d;
  --yellow:#ffd200;
  --band:#efefef;
  --line:#dcdcdc;
  --blue:#1b86c6;
  --footer:#0f6aa8;
  --footer-bar:#1b2a3b;
  --white:#fff;
}
*{box-sizing:border-box;margin:0;padding:0}
html,body{width:1200px;height:2397px;overflow:hidden}
body{position:relative;background:var(--white);font-family:"Open Sans",Arial,sans-serif;color:var(--ink)}
.abs{position:absolute}
a{color:inherit;text-decoration:none}

/* header */
.utility{left:722px;top:0;width:368px;height:26px;background:#f4f4f4;border:1px solid #d6d6d6;border-top:0;font-size:11px;color:#444;display:flex;align-items:center;padding:0 10px;gap:8px}
.utility .phone{margin-left:auto;display:flex;align-items:center;gap:5px}
.brand{left:112px;top:32px;display:flex;align-items:center;gap:14px}
.brand .dot{width:44px;height:44px;border-radius:50%;background:var(--red)}
.brand .name{font-size:20px;font-weight:600;letter-spacing:5px;color:#222;text-transform:uppercase;line-height:1}
.mainnav{left:0;top:99px;width:1200px;height:42px;background:var(--nav)}
.mainnav ul{list-style:none;position:absolute;left:121px;top:0;display:flex;gap:46px;line-height:42px;color:#fff;font-size:15px}
.search{left:802px;top:105px;width:251px;height:32px;background:#fff;border:1px solid #ccc;font-size:12px;color:#888;padding:7px 10px}
.search-btn{left:1053px;top:105px;width:37px;height:32px;background:var(--red);display:flex;align-items:center;justify-content:center}

/* hero */
.hero{left:0;top:141px;width:1200px;height:441px;background:radial-gradient(ellipse 60% 70% at 50% 40%,#2fa6e6 0%,#1b7fc2 45%,transparent 80%),linear-gradient(180deg,var(--hero-a),var(--hero-b) 55%,#0e5f9e)}
.slide-panel{left:109px;top:251px;width:981px;height:297px;background:rgba(16,36,56,.88)}
.tablet{left:179px;top:187px;width:441px;height:361px;background:#111;border:3px solid #cfcfcf;border-bottom:0;border-radius:22px 22px 0 0}
.tablet .screen{position:absolute;left:47px;top:52px;width:341px;height:309px;background:radial-gradient(circle at 35% 45%,#f4f6f8 0 18%,transparent 30%),radial-gradient(circle at 70% 30%,#3a5570 0,transparent 45%),linear-gradient(135deg,#dfe3e7,#8e98a2 55%,#2b3038)}
.slide-copy{left:639px;top:280px;width:430px;color:#fff}
.slide-copy h1{font-size:32px;font-weight:700;line-height:1.1}
.slide-copy h2{font-size:19px;font-weight:400;margin-top:2px}
.slide-copy p{font-size:13.5px;line-height:20px;margin-top:22px;color:#e8eef4;width:430px}
.btn-yellow{left:639px;top:471px;width:134px;height:40px;border-radius:20px;background:linear-gradient(#ffe24a,var(--yellow) 60%,#e9b800);color:#333;font-size:16px;display:flex;align-items:center;justify-content:center}
.arrow{top:420px;width:30px;height:38px}
.tabs{left:109px;top:548px;width:981px;height:83px;background:var(--tabs);display:flex;box-shadow:0 22px 26px -10px rgba(0,0,0,.35)}
.tab{display:flex;align-items:center;gap:12px;padding-left:16px;color:#fff;font-size:13px;font-weight:600;text-transform:uppercase;line-height:17px;border-right:1px solid #444}
.tab:last-child{border-right:0}

/* difference */
.diff-photo{left:110px;top:741px;width:301px;height:181px;background:radial-gradient(ellipse 70% 45% at 40% 70%,#e8e2d2 0,transparent 70%),linear-gradient(180deg,#c3cad0,#7b838b 45%,#3a3e44)}
.diff-person{left:400px;top:687px;width:103px;height:256px;background:linear-gradient(180deg,#d8c3ae 0 16%,#e9eaec 16% 24%,#1b2230 24%)}
.diff-copy{left:527px;top:738px;width:525px}
.diff-copy h3{font-size:22px;font-weight:400;color:#222}
.diff-copy p{font-size:13px;line-height:20px;color:var(--text);margin-top:10px}
.btn-red{left:529px;top:898px;width:112px;height:30px;background:var(--red);color:#fff;font-size:13px;display:flex;align-items:center;justify-content:center;border-radius:2px}

/* services */
.section-title{font-size:22px;font-weight:400;color:#2b2b2b}
.services-title{left:109px;top:988px}
.services-rule{left:109px;top:1026px;width:981px;height:1px;background:var(--line)}
.pager{left:1031px;top:989px;width:56px;height:24px;display:flex;gap:2px}
.pager span{flex:1;background:#3f4245;border-radius:3px;display:flex;align-items:center;justify-content:center}
.card{top:1047px;width:310px}
.card .pic{height:164px}
.card .label{height:63px;background:#f4f4f4;border-bottom:2px solid #dedede;font-size:18px;color:#333;display:flex;align-items:center;justify-content:center}
.card.active .label{border-bottom-color:var(--red)}

/* news */
.news-band{left:0;top:1304px;width:1200px;height:384px;background:var(--band)}
.news-title{left:109px;top:1324px}
.news-view{left:576px;top:1338px;font-size:11px;color:#333}
.news-rule{left:109px;top:1360px;width:509px;height:1px;background:#cfcfcf}
.news-item{left:113px;width:505px}
.date{position:absolute;left:0;top:0;width:61px;text-align:center}
.date .d{height:32px;background:var(--red);color:#fff;font-size:20px;line-height:32px}
.date .m{height:35px;background:#dcdcdc;color:#555;font-size:16px;line-height:35px}
.news-item h4{margin-left:79px;font-size:16px;font-weight:400;color:#222}
.news-item p{margin-left:79px;font-size:12.5px;line-height:20px;color:var(--text);margin-top:2px;width:430px}
.news-sep{left:110px;top:1505px;width:508px;height:1px;background:#d6d6d6}
.video{left:652px;top:1369px;width:427px;height:272px;background:radial-gradient(ellipse 55% 40% at 55% 55%,#2e3238 0 60%,transparent 75%),linear-gradient(180deg,#9fb4c6 0,#6b8093 40%,#3b4450 65%,#1f4d6e 85%,#173a55);border:1px solid #222}
.video .bar{position:absolute;left:0;bottom:0;width:100%;height:18px;background:#111}

/* industries */
.ind{left:112px;width:620px}
.ind .thumb{position:absolute;left:0;top:0;width:97px;height:107px}
.ind h3{margin-left:110px;font-size:20px;font-weight:400;color:#222}
.ind p,.ind li{margin-left:110px;font-size:12.5px;line-height:16px;color:#999}
.ind ul{list-style:none;margin-top:10px}
.ind .more{margin-left:110px;margin-top:12px;display:inline-block;font-size:12px;color:#777;text-decoration:underline;letter-spacing:.5px}
.ind-sep{left:110px;top:1873px;width:622px;height:1px;background:#ddd}
.contact-title{left:826px;top:1731px;font-size:20px;font-weight:600;color:#222}
.form{left:821px;top:1764px;width:253px;height:237px;border:1px solid #e2e2e2;padding:5px}
.field{height:29px;background:#e6e6e6;margin-bottom:6px;font-size:11px;color:#777;padding:7px 8px}
.field.msg{height:118px}
.send{left:823px;top:2012px;width:77px;height:29px;background:var(--blue);color:#fff;font-size:13px;font-weight:700;display:flex;align-items:center;justify-content:center}

/* footer */
.site-footer{color:var(--white)}
.footer{left:0;top:2081px;width:1200px;height:278px;background:var(--footer);box-shadow:inset 0 14px 18px -12px rgba(0,0,0,.45)}
.fcol{top:2131px;color:var(--white)}
.fcol h5{font-size:20px;font-weight:600;text-transform:uppercase;letter-spacing:.2px;color:var(--white)}
.fcol ul{list-style:none;margin-top:10px}
.fcol li{font-size:12.5px;line-height:20px;color:var(--white)}
.fbrand{display:flex;align-items:center;gap:10px;margin-top:14px}
.fbrand .dot{width:30px;height:30px;border-radius:50%;background:#fff}
.fbrand .name{font-size:12px;letter-spacing:3px;font-weight:600;text-transform:uppercase}
.fcol p{font-size:12.5px;line-height:19px;margin-top:18px;width:215px;color:var(--white)}
.footbar{left:0;top:2359px;width:1200px;height:38px;background:var(--footer-bar);color:#fff;font-size:12px}
.footbar .copy{position:absolute;left:112px;line-height:38px}
.footbar ul{position:absolute;right:110px;list-style:none;display:flex;line-height:38px}
.footbar li+li:before{content:"|";margin:0 11px;color:#fff}
.footbar .current{color:#3aa0e6}
</style>
</head>
<body>

<header>
  <div class="abs utility">
    <a href="#">Company</a>|<a href="#">Careers</a>|<a href="#">Contact Us</a>
    <span class="phone"><svg width="12" height="14" viewBox="0 0 12 14"><path d="M3 1l2 3-1.5 1.5c.6 1.8 1.7 3 3.2 3.8L8 8l3 2-1 2.5C5 12 1 7 1 2z" fill="#555"/></svg>021-555-0142-77</span>
  </div>
  <div class="abs brand"><span class="dot"></span><span class="name">Northvale<br><span style="font-size:13px;letter-spacing:7px">Logistics</span></span></div>
  <nav class="abs mainnav"><ul><li>Solutions</li><li>Our Process</li><li>Industries</li></ul></nav>
  <div class="abs search">Search</div>
  <div class="abs search-btn"><svg width="16" height="16" viewBox="0 0 16 16"><circle cx="6.5" cy="6.5" r="5" fill="none" stroke="#fff" stroke-width="2"/><path d="M10 10l5 5" stroke="#fff" stroke-width="2"/></svg></div>
</header>

<section class="abs hero" role="img" aria-label="Blue technology backdrop with circuit lines"></section>
<div class="abs slide-panel"></div>
<div class="abs tablet"><div class="screen" role="img" aria-label="Photo of a businessman touching a holographic network of icons on a screen"></div></div>
<div class="abs slide-copy">
  <h1>A New Way To Think</h1>
  <h2>About Supply Chain Transformation</h2>
  <p>Northvale Transform supply chains by managing complexity, providing data-driven insights and implementing forward-thinking innovation and actionable strategies that change business results.</p>
</div>
<a class="abs btn-yellow" href="#">Read More</a>
<svg class="abs arrow" style="left:80px" viewBox="0 0 30 38"><path d="M22 4L8 19l14 15" fill="none" stroke="#fff" stroke-width="4"/></svg>
<svg class="abs arrow" style="left:1090px" viewBox="0 0 30 38"><path d="M8 4l14 15L8 34" fill="none" stroke="#fff" stroke-width="4"/></svg>
<div class="abs tabs">
  <div class="tab" style="width:243px"><svg width="34" height="34" viewBox="0 0 34 34"><circle cx="17" cy="17" r="11" fill="none" stroke="#fff" stroke-width="5" stroke-dasharray="4 3"/><circle cx="17" cy="17" r="5" fill="#fff"/></svg>Material Management<br>&amp; Factory Support</div>
  <div class="tab" style="width:252px"><svg width="36" height="30" viewBox="0 0 36 30"><circle cx="18" cy="15" r="12" fill="none" stroke="#fff" stroke-width="2.5"/><path d="M6 15h24M18 3v24" stroke="#fff" stroke-width="2"/></svg>Retail &amp; E-Commerce<br>Distribution</div>
  <div class="tab" style="width:238px"><svg width="30" height="30" viewBox="0 0 30 30"><path d="M4 4l22 22M26 4L4 26" stroke="#fff" stroke-width="4"/></svg>Aftermarket Support</div>
  <div class="tab" style="width:248px"><svg width="32" height="32" viewBox="0 0 32 32"><circle cx="16" cy="16" r="10" fill="none" stroke="#fff" stroke-width="5" stroke-dasharray="4 3"/><circle cx="16" cy="16" r="4" fill="#fff"/></svg>Critical Logistics</div>
</div>

<section>
  <div class="abs diff-photo" role="img" aria-label="Photo of a large industrial hall with machinery"></div>
  <div class="abs diff-person" role="img" aria-label="Photo of a businessman in a dark suit with arms folded"></div>
  <div class="abs diff-copy">
    <h3>The Northvale Difference</h3>
    <p>Lorem Ipsum is simply dummy text of the printing and typesetting industry. Lorem Ipsum has been the industry's standard dummy text ever since the 1500s, when an unknown printer took a galley of type and scrambled it to make a type specimen book. It has survived not only five centuries, but also the leap into electronic typesetting, remaining essentially unchanged.</p>
  </div>
  <a class="abs btn-red" href="#">Read More</a>
</section>

<section>
  <h3 class="abs section-title services-title">Our Services</h3>
  <div class="abs services-rule"></div>
  <div class="abs pager"><span><svg width="6" height="8"><path d="M5 0v8L0 4z" fill="#fff"/></svg></span><span><svg width="6" height="8"><path d="M1 0v8l5-4z" fill="#fff"/></svg></span></div>
  <div class="abs card" style="left:110px"><div class="pic" role="img" aria-label="Photo of a business team gathered around a laptop" style="background:radial-gradient(ellipse 80% 55% at 50% 85%,#2a2d35 0,#4a4e58 45%,transparent 75%),linear-gradient(180deg,#f5f5f5,#dcdfe3)"></div><div class="label">Factory Support</div></div>
  <div class="abs card active" style="left:447px"><div class="pic" role="img" aria-label="Photo of cardboard boxes on a conveyor line" style="background:radial-gradient(ellipse 45% 35% at 60% 45%,#d7ae76 0,transparent 70%),linear-gradient(180deg,#5e4a36,#b88c58 45%,#7d7f82 75%,#4b4d50)"></div><div class="label">Retail Distributions</div></div>
  <div class="abs card" style="left:781px"><div class="pic" role="img" aria-label="Photo of a smiling support agent with a headset" style="background:radial-gradient(ellipse 40% 60% at 68% 50%,#efc9a6 0,#b8764a 55%,transparent 80%),linear-gradient(90deg,#e4ebf2,#c9d3dd 45%,#8a5634)"></div><div class="label">After Markit Support</div></div>
</section>

<section>
  <div class="abs news-band"></div>
  <h3 class="abs section-title news-title">Recent News</h3>
  <a class="abs news-view" href="#">View All</a>
  <div class="abs news-rule"></div>
  <article class="abs news-item" style="top:1382px">
    <div class="date"><div class="d">27</div><div class="m">Mar</div></div>
    <h4>Lorem ipsum dolor sit amet</h4>
    <p>Lorem Ipsum is simply dummy text of the printing and typesetting industry. Lorem Ipsum has been the industry's standard dummy text ever since the 1500s, when an unknown printer took a galley of type and scrambled it to make a type specimen book.</p>
  </article>
  <div class="abs news-sep"></div>
  <article class="abs news-item" style="top:1527px">
    <div class="date"><div class="d">27</div><div class="m">Mar</div></div>
    <h4>Lorem ipsum dolor sit amet</h4>
    <p>Lorem Ipsum is simply dummy text of the printing and typesetting industry. Lorem Ipsum has been the industry's standard dummy text ever since the 1500s, when an unknown printer took a galley of type and scrambled it to make a type specimen book.</p>
  </article>
  <div class="abs video" role="img" aria-label="Video still of an offshore supply ship at sea">
    <svg style="position:absolute;left:184px;top:110px" width="56" height="56" viewBox="0 0 56 56"><circle cx="28" cy="28" r="27" fill="#111"/><path d="M22 16l18 12-18 12z" fill="#fff"/></svg>
    <div class="bar"><div style="position:absolute;left:0;top:-4px;width:100px;height:4px;background:var(--red)"></div></div>
  </div>
</section>

<section>
  <div class="abs ind" style="top:1734px">
    <div class="thumb" role="img" aria-label="Photo of a technician at a control panel" style="background:linear-gradient(135deg,#d8d4a0,#8a8f7c 55%,#4b4f44)"></div>
    <h3>Industries We Serve</h3>
    <p style="margin-top:10px;width:470px">Our in-place DC network and logistics systems allow retailers and e-commerce companies to leverage our national footprint to provide responsive customer service</p>
    <a class="more" href="#">READ MORE</a>
  </div>
  <div class="abs ind-sep"></div>
  <div class="abs ind" style="top:1900px">
    <div class="thumb" role="img" aria-label="Photo of industrial chimneys under a blue sky" style="background:linear-gradient(180deg,#3f78b8,#a9c6e2 55%,#6c6f72)"></div>
    <h3>A Different Perspective</h3>
    <ul>
      <li>•We commit our own capital and resources to align with our clients' goals</li>
      <li>•Unlike consultants, we implement and operate the solutions we design</li>
      <li>•We guarantee business performance for our clients by investing in and executing the solutions we design.</li>
    </ul>
  </div>
  <h3 class="abs contact-title">Contact Us</h3>
  <form class="abs form">
    <div class="field">Name:</div>
    <div class="field">Last Name:</div>
    <div class="field">Email address:</div>
    <div class="field msg">Message:</div>
  </form>
  <a class="abs send" href="#">SEND</a>
</section>

<footer class="site-footer">
  <div class="abs footer"></div>
  <div class="abs fcol" style="left:113px">
    <h5>About Company</h5>
    <div class="fbrand"><span class="dot"></span><span class="name">Northvale Logistics</span></div>
    <p>Lorem ipsum dolor sit amet consectetur adipisicing elit eiusmod tempor incididunt ut labore et dolore magna aliqua ad minim veniam quis nostrud exercitation ullam.</p>
  </div>
  <div class="abs fcol" style="left:382px">
    <h5>Our Process</h5>
    <ul><li>Concept of operations</li><li>Supplying the infrastructure</li><li>Analyzing the data</li><li>Managing complexity</li><li>Providing actionable strategies</li><li>Nvesting in our client's success</li><li>Driving business results</li></ul>
  </div>
  <div class="abs fcol" style="left:644px">
    <h5>Our Solutions</h5>
    <ul><li>Business Analytics</li><li>Geographic Coverage</li><li>Project financing</li><li>Project implementation</li><li>Technology</li><li>Quality</li></ul>
  </div>
  <div class="abs fcol" style="left:885px">
    <h5>Industries We Serve</h5>
    <ul><li>Aerospace</li><li>defense</li><li>Industrial</li><li>Manufacturing</li><li>Media and Entertainment</li><li>Medical</li><li>Retail</li><li>Telecom &amp; Electroincs</li></ul>
  </div>
  <div class="abs footbar">
    <span class="copy">Copyright ©2014 Northvale. All Rights Reserved.</span>
    <ul><li class="current">Home</li><li>Careers</li><li>Solutions</li><li>Our Process</li><li>Industries</li><li>Contact Us</li></ul>
  </div>
</footer>

</body>
</html>
```